Business card design for my company.
I would like the card's background colour to be black. You can also see our web site to get an idea of our brand. https://www.tmwhomecrafting.com.au/
- Name
- Email

```html
<!DOCTYPE html>
<html lang="en">
<head>
<meta charset="utf-8">
<title>TMW Home Crafting – Business Card</title>
<link href="https://fonts.googleapis.com/css2?family=Montserrat:wght@400;700&display=swap" rel="stylesheet">
<style>
  :root {
    --stage: #2a2a2a;
    --card: #1f1f1f;
    --green: #1f9a45;
    --white: #f2f2f2;
    --muted: #d8d8d8;
  }
  * { margin: 0; padding: 0; box-sizing: border-box; }
  html, body {
    width: 1200px;
    height: 801px;
    overflow: hidden;
    background: var(--stage);
    font-family: "Montserrat", Arial, sans-serif;
  }
  .canvas {
    position: relative;
    width: 1200px;
    height: 801px;
    display: flex;
    align-items: center;
    justify-content: center;
    gap: 60px;
  }
  .card {
    position: relative;
    width: 520px;
    height: 300px;
    background: var(--card);
    border-radius: 18px;
    box-shadow: 0 14px 30px rgba(0,0,0,0.45);
    overflow: hidden;
  }

  /* Front */
  .accent-bar {
    position: absolute;
    left: 0;
    top: 68px;
    width: 16px;
    height: 34px;
    background: var(--green);
  }
  .person {
    position: absolute;
    left: 32px;
    top: 64px;
  }
  .person-name {
    color: var(--green);
    font-weight: 700;
    font-size: 22px;
    letter-spacing: 0.5px;
    text-transform: uppercase;
    line-height: 1.1;
    white-space: nowrap;
  }
  .person-role {
    color: var(--muted);
    font-size: 13px;
    margin-top: 3px;
  }
  .brand-mini {
    position: absolute;
    right: 34px;
    top: 40px;
    width: 190px;
    display: flex;
    align-items: center;
    gap: 12px;
  }
  .brand-square {
    width: 14px;
    height: 14px;
    flex: none;
    background: var(--green);
  }
  .brand-name {
    color: var(--white);
    font-weight: 700;
    font-size: 18px;
    line-height: 1.3;
    letter-spacing: 2px;
    text-transform: uppercase;
  }
  .contact-list {
    position: absolute;
    left: 150px;
    bottom: 34px;
    list-style: none;
  }
  .contact-item {
    display: flex;
    align-items: center;
    gap: 10px;
    color: var(--white);
    font-size: 14px;
    line-height: 26px;
    white-space: nowrap;
  }
  .contact-icon { width: 13px; height: 13px; flex: none; }

  /* Back */
  .card-back {
    display: flex;
    align-items: center;
    justify-content: center;
  }
  .brand-large {
    display: flex;
    align-items: center;
    gap: 16px;
  }
  .brand-large .brand-square { width: 22px; height: 22px; }
  .brand-large .brand-name { font-size: 30px; letter-spacing: 3px; white-space: nowrap; }
</style>
</head>
<body>
<main class="canvas">
  <section class="card card-front" aria-label="Business card front">
    <span class="accent-bar"></span>
    <div class="person">
      <p class="person-name">Darren Kells</p>
      <p class="person-role">CEO/Founder</p>
    </div>
    <div class="brand-mini">
      <span class="brand-square"></span>
      <span class="brand-name">TMW Home Crafting</span>
    </div>
    <ul class="contact-list">
      <li class="contact-item">
        <svg class="contact-icon" viewBox="0 0 16 16" aria-hidden="true"><path fill="#1f9a45" d="M3.5 1l2.5 3-1.5 1.8c.9 2 2.5 3.6 4.5 4.5L10.8 8.8 14 11.3 12.5 14.5C6.5 14 2 9.5 1.5 3.5z"/></svg>
        897-555-0142
      </li>
      <li class="contact-item">
        <svg class="contact-icon" viewBox="0 0 16 16" aria-hidden="true"><rect x="1" y="3" width="14" height="10" fill="#1f9a45"/><path d="M1 3l7 6 7-6" fill="none" stroke="#1f1f1f" stroke-width="1.4"/></svg>
        info@tmwhomecrafting.com.au
      </li>
      <li class="contact-item">
        <svg class="contact-icon" viewBox="0 0 16 16" aria-hidden="true"><circle cx="8" cy="8" r="7" fill="#1f9a45"/><path d="M1 8h14M8 1v14M3 4.5h10M3 11.5h10" stroke="#1f1f1f" stroke-width="0.9" fill="none"/><ellipse cx="8" cy="8" rx="3" ry="7" fill="none" stroke="#1f1f1f" stroke-width="0.9"/></svg>
        www.tmwhomecrafting.com.au
      </li>
    </ul>
  </section>

  <section class="card card-back" aria-label="Business card back">
    <div class="brand-large">
      <span class="brand-square"></span>
      <span class="brand-name">TMW Home Crafting</span>
    </div>
  </section>
</main>
</body>
</html>
```